Backdrop Banner to be designed for a kids handwriting company

We are an occupational therapy company that helps children improve their handwriting. We give online lessons and make how-to videos for the kids to watch. We are looking for a backdrop to be designed that can be placed on a roller blind to use when needed. Size to be 183cm (width) x200cm (height). The final design needs to be produced in a format that can be uploaded to a printing company for them to produce.

We need our logo to be displayed. Our corporate colours are: #ff0069, #2abeb0, #ffc700, #93db40, #322e58. If you wish to see our current 'look' go to www.penpathlearning.co.uk. We can tell you our fonts if asked.

We work with children aged 6 to 16 years, mainly 10 to 13 years. In the past, I have placed motivational stickers on the back of my wall. Many of the children we see have lost confidence in themselves hence the words 'Believe in yourself', 'Make it happen' etc. were chosen. We teach them how to write clearly so the teachers can read/mark their work, parents are happy and we boost their self confidence. We are open to positive words or doodle style images but they cannot be cutesy. The backdrop must not overpower a lesson and take away the kid's focus.

I have included some ideas, our logo and a picture of what is the backdrop in my office.
1. We are open to keeping everything in the right-hand corner of the screen so the kids see us and any image is to the right (as per the picture). If doing this the images will need to sit from 30cm to 80cm from the top of the blind when fully down. Width needed is probably 65cm.
2. We are open to the parkour concept of words and images going across the whole backdrop or on the right hand side.
3. We are open to the backdrop having one image on its own whether that be random or specific images.
4. If using any writing the font has to be readable, no imitation of 'bad' handwriting. We see kids at any time of the day so we cannot have it say 'Good morning'.

We are hoping you will be inspired by this project as we'd love to work with you and see your ideas.

UPDATE 1 - 03.08.23: Based on the designs submitted so far please watch the wording of any motivational words and keep in mind this is a backdrop banner only the top half is likely to be seen on screen and there will be a person sitting in front of your design.

UPDATE 2 - 04.08.23: Mock up images with measurements added to help you design this backdrop for a video.

UPDATE: Based on the designs submitted so far please watch the wording of any motivational words and keep in mind this is a backdrop banner only the top half is likely to be seen on screen and there will be a person sitting in front of your design.

Supplied this in the brief

Other font styles liked:
• Business fonts on website are Kind Heart, Logo is Typo Round Regular

• Supplied this in the brief

```html
<!DOCTYPE html>
<html lang="en">
<head>
<meta charset="utf-8">
<title>PenPath Learning – Make It Happen</title>
<link href="https://fonts.googleapis.com/css2?family=Luckiest+Guy&family=Lilita+One&family=Fredoka:wght@600&family=Roboto:wght@500;700&display=block" rel="stylesheet">
<style>
  :root {
    --teal: #3cbfb2;
    --teal-deep: #2fb0a3;
    --teal-shadow: #1f7f77;
    --navy: #312d57;
    --yellow: #ffc700;
    --green: #93c547;
    --pink: #ff0069;
    --white: #ffffff;
    --pencil: #f2ac2c;
    --backpack: #2d68b8;
    --red-art: #d23a3e;
    --orange-art: #f29a26;
  }
  html, body {
    margin: 0;
    padding: 0;
    width: 854px;
    height: 1200px;
    overflow: hidden;
    background: var(--navy);
  }
  .banner {
    position: relative;
    width: 854px;
    height: 1200px;
    overflow: hidden;
    background: var(--navy);
    font-family: "Luckiest Guy", "Lilita One", sans-serif;
    font-weight: 400;
  }
  .doodle-field {
    position: absolute;
    inset: 0;
    background: linear-gradient(180deg, var(--teal) 0%, var(--teal-deep) 100%);
  }
  .navy-flow {
    position: absolute;
    inset: 0;
  }
  .brand-name {
    position: absolute;
    top: 70px;
    left: 0;
    right: 0;
    text-align: center;
    font-family: "Fredoka", sans-serif;
    font-weight: 600;
    font-size: 34px;
    line-height: 40px;
    color: var(--white);
    letter-spacing: 1px;
  }
  .pencil-art {
    position: absolute;
    left: 176px;
    top: 138px;
    width: 460px;
    height: 64px;
    background: var(--pencil);
  }
  .headline {
    position: absolute;
    left: 0;
    right: 0;
    top: 218px;
    margin: 0;
    text-align: center;
    font-weight: 400;
    font-size: 132px;
    line-height: 116px;
    color: var(--white);
    text-shadow: 6px 6px 0 var(--teal-shadow);
  }
  .tagline {
    position: absolute;
    left: 0;
    right: 0;
    top: 478px;
    text-align: center;
    font-size: 54px;
    line-height: 54px;
    color: var(--yellow);
    text-shadow: 3px 3px 0 var(--teal-shadow);
  }
  .promise {
    position: absolute;
    left: 34px;
    top: 742px;
    width: 280px;
    text-align: center;
    font-size: 44px;
    line-height: 50px;
    color: var(--yellow);
  }
  .backpack-art {
    position: absolute;
    left: 332px;
    top: 736px;
    width: 188px;
    height: 252px;
    background: var(--backpack);
  }
  .age-badge {
    position: absolute;
    left: 590px;
    top: 694px;
    width: 220px;
    height: 220px;
  }
  .age-badge-text {
    position: absolute;
    left: 590px;
    top: 774px;
    width: 220px;
    text-align: center;
    font-size: 18px;
    line-height: 23px;
    color: var(--white);
    letter-spacing: 0.5px;
  }
  .services {
    position: absolute;
    left: 0;
    right: 0;
    top: 1017px;
    text-align: center;
    font-family: "Roboto", sans-serif;
    font-weight: 500;
    font-size: 17.5px;
    line-height: 22px;
    letter-spacing: 0.6px;
    color: var(--green);
  }
  .closing-line {
    position: absolute;
    left: 0;
    right: 0;
    top: 1046px;
    text-align: center;
    font-size: 41px;
    line-height: 44px;
    color: var(--yellow);
    letter-spacing: 0.5px;
  }
  .closing-sub {
    position: absolute;
    left: 0;
    right: 0;
    top: 1092px;
    text-align: center;
    font-family: "Roboto", sans-serif;
    font-weight: 700;
    font-size: 29px;
    line-height: 34px;
    letter-spacing: 1.5px;
    color: var(--green);
  }
  .web-address {
    position: absolute;
    left: 0;
    right: 0;
    top: 1136px;
    text-align: center;
    font-family: "Roboto", sans-serif;
    font-weight: 700;
    font-size: 19px;
    line-height: 24px;
    letter-spacing: 0.6px;
    color: var(--yellow);
  }
  .corner-art {
    position: absolute;
  }
  .corner-art.left-top {
    left: 0;
    top: 980px;
    width: 90px;
    height: 90px;
    background: var(--red-art);
  }
  .corner-art.left-bottom {
    left: 0;
    top: 1110px;
    width: 78px;
    height: 90px;
    background: var(--red-art);
  }
  .corner-art.right-top {
    left: 798px;
    top: 1016px;
    width: 56px;
    height: 54px;
    background: var(--orange-art);
  }
  .corner-art.right-bottom {
    left: 738px;
    top: 1100px;
    width: 116px;
    height: 100px;
    background: var(--orange-art);
  }
</style>
</head>
<body>
<main class="banner">
  <div class="doodle-field" role="img" aria-label="Teal ruled notebook paper covered in faint school doodles"></div>

  <svg class="navy-flow" width="854" height="1200" viewBox="0 0 854 1200" aria-hidden="true">
    <path d="M0,428 C40,470 70,556 140,556 L286,552 C338,552 350,746 386,746 L468,746 C504,746 514,554 562,552 L744,556 C802,556 820,470 854,432 L854,1200 L0,1200 Z"
          fill="var(--navy)" stroke="var(--white)" stroke-width="4"/>
  </svg>

  <div class="brand-name">PenPath Learning</div>

  <div class="pencil-art" role="img" aria-label="Illustration of a long yellow pencil"></div>

  <h1 class="headline">MAKE IT<br>HAPPEN</h1>
  <div class="tagline">BELIEVE IN YOURSELF</div>

  <div class="promise">MAKE IT<br>READBLE<br>IN 66 DAYS</div>

  <div class="backpack-art" role="img" aria-label="Illustration of a blue school backpack"></div>

  <svg class="age-badge" viewBox="-110 -110 220 220" aria-hidden="true">
    <polygon fill="var(--pink)" points="104,0 86.9,13.7 98.9,32.1 78.4,40 84.1,61.2 62.2,62.2 61.2,84.1 40,78.4 32.1,98.9 13.7,86.9 0,104 -13.7,86.9 -32.1,98.9 -40,78.4 -61.2,84.1 -62.2,62.2 -84.1,61.2 -78.4,40 -98.9,32.1 -86.9,13.7 -104,0 -86.9,-13.7 -98.9,-32.1 -78.4,-40 -84.1,-61.2 -62.2,-62.2 -61.2,-84.1 -40,-78.4 -32.1,-98.9 -13.7,-86.9 0,-104 13.7,-86.9 32.1,-98.9 40,-78.4 61.2,-84.1 62.2,-62.2 84.1,-61.2 78.4,-40 98.9,-32.1 86.9,-13.7"/>
  </svg>
  <div class="age-badge-text">HANDWRITTING<br>LESSONS<br>6–16 YEARS</div>

  <div class="services">EXAM READY HANDWRITTING - COURSES - ONLINE LESSONS</div>
  <div class="closing-line">YOU CAN NEVER HAVE ENOUGH</div>
  <div class="closing-sub">PARKOUR SKILLS</div>
  <div class="web-address">www.penpathlearning.co.uk</div>

  <div class="corner-art left-top" role="img" aria-label="Illustration of a red pencil"></div>
  <div class="corner-art left-bottom" role="img" aria-label="Illustration of a red ruler"></div>
  <div class="corner-art right-top" role="img" aria-label="Illustration of an orange pencil tip"></div>
  <div class="corner-art right-bottom" role="img" aria-label="Illustration of an orange notebook"></div>
</main>
</body>
</html>
```